Very new and innovative Web design for Property managers of Vacation rentals

We are looking for a new website design for travel agencies and property managers specialised on vacation rentals business, holiday villas and apartments.

The end users of this website are travellers who are looking for a vacation home for their next holiday: this is the reason why the website must be easy to use, attractive, professional, possibly elegant and focused on get new reservations.

This is a draft of our current website: https://intro3.kelumsito.com/
Please consider that we would like to have proposals with a totally different and innovative layout, surprise us!

These are the pages of the website:
• Homepage: feel free to redesign all the homepage as you wish, surprise us with something very new! Please consider that Property manager/Travel agencies usually want to have the opportunity to put in evidence groups of houses with specific characteristics (eg. villas with private swimming pool, apartment in big/small towns, villas with air co, etc…), destinations and tourist areas, and sometimes experiences or activities (please consider that the website layout must be suitable even if some of the previous sections are not used).
• Search page: we’d like to organise the results of the search page in three different ways:
o Grid
o Map
o List
• Property page: to illustrate the characteristics, descriptions, images, …. of the property. It is very important to put in evidence images of the property and to maintain the booking form (and the other call to action bottom – eg. whatsapp) always visible
• Custom pages: static pages composed usually by text, images and call to actions
• Contact us (general form)
• Info request (specific of a property form)
• Booking process
• Blog, organised in four pages:
o Home Page – introduction to the blog
o List of articles
o Single article
o Site Map (presentation of categories and sub-categories)

If possible, we’d prefer to receive the material in Adobe XD or similar so that we can obtain the three versions:
- smartphone
- tablet
- desktop

The website will be then developed in Bootstrap: as a result we’ll need the icons in SVG format (or the library used)

In attachment you can find the map of the website pages

```html
<!DOCTYPE html>
<html lang="en">
<head>
<meta charset="utf-8">
<title>Contact Us – StayHarbor</title>
<link rel="stylesheet" href="https://fonts.googleapis.com/css2?family=Oswald:wght@300;400;500;600&family=Poppins:ital,wght@0,300;0,400;0,500;0,600;1,400&display=swap">
<style>
:root{
  --green:#17b27c;
  --green-dark:#12986a;
  --ink:#222;
  --muted:#555;
  --line:#555;
  --footer:#1b1b1c;
  --footer-line:#3a3a3a;
  --white:#fff;
}
*{box-sizing:border-box;margin:0;padding:0}
html,body{width:716px;height:1200px;overflow:hidden;background:var(--white)}
body{position:relative;font-family:'Poppins',sans-serif;color:var(--ink)}
.abs{position:absolute}

/* header */
.topbar{left:519px;top:0;width:197px;height:21px;background:var(--green);clip-path:polygon(0 0,100% 0,100% 100%,21px 100%)}
.topbar-item{top:7px;font-size:5.6px;font-weight:500;color:var(--white);display:flex;align-items:center;gap:2px}
.brand{left:60px;top:14px;display:flex;align-items:center;gap:4px;font-size:14px;color:#333}
.brand-mark{width:20px;height:20px;background:var(--green);border-radius:50%}
.nav-item{top:32px;font-size:6.4px;color:#333}
.nav-item.active{color:var(--green);font-weight:500}

/* hero */
.hero{left:0;top:56px;width:716px;height:146px;background:linear-gradient(180deg,#4e4a3f 0%,#3c4650 55%,#2d3c46 100%)}
.hero-title{left:0;top:144px;width:716px;text-align:center;font-family:'Oswald',sans-serif;font-weight:500;font-size:23px;color:var(--white);letter-spacing:-.2px}

/* content */
.crumbs{left:55px;top:223px;font-size:6.5px;color:#777}
.crumbs b{font-weight:500;color:var(--ink)}
.page-title{left:55px;top:240px;font-family:'Oswald',sans-serif;font-weight:300;font-size:23px;color:var(--ink)}
.lead{left:55px;top:272px;width:400px;font-size:7.8px;line-height:11.6px;color:var(--muted)}
.office-name{left:56px;top:316px;font-family:'Oswald',sans-serif;font-weight:300;font-size:13.5px}
.office-row{left:56px;display:flex;gap:4px;font-size:7.2px;line-height:9px;color:#333}
.office-row svg{flex:none;margin-top:1px}

.field{border:0.8px solid var(--line);font-size:5.6px;color:#666;padding:8px 6px}
.field.tall{padding-top:5px}
.subscribe{left:291px;top:450px;display:flex;align-items:center;gap:6px;font-size:6.4px;font-style:italic;color:#444}
.box{width:8px;height:8px;border:0.6px solid #aaa}
.captcha{left:291px;top:468px;width:91px;height:23px;border:0.6px solid #d4d4d4;background:#f9f9f9;box-shadow:0 0 2px rgba(0,0,0,.08)}
.send{left:291px;top:501px;width:53px;height:22px;background:var(--green);color:var(--white);font-size:6px;font-weight:500;display:flex;align-items:center;justify-content:center}

/* map */
.map{left:0;top:585px;width:716px;height:249px;background:linear-gradient(135deg,#eef0ee 0%,#e8ebe7 60%,#dfe6ea 100%)}

/* footer */
.footer{left:0;top:834px;width:716px;height:366px;background:var(--footer);color:var(--white)}
.f-brand{left:57px;top:890px;display:flex;align-items:center;gap:4px;font-size:15px;font-weight:500;letter-spacing:.6px;color:var(--white)}
.f-brand .dot{width:22px;height:22px;border-radius:50%;background:var(--green)}
.f-sub{left:57px;top:930px;font-size:7.4px;font-weight:500;letter-spacing:.6px;color:var(--white)}
.f-sub-line{left:56px;top:945px;width:125px;height:1px;background:var(--white)}
.f-text{left:57px;top:960px;width:190px;font-size:7.3px;line-height:11px;letter-spacing:.5px;color:#ddd}
.f-head{top:878px;font-size:8.8px;font-weight:500;letter-spacing:.9px;color:var(--green)}
.f-link{left:309px;font-size:7.3px;letter-spacing:.7px;color:#eee}
.post-thumb{left:472px;width:42px;height:36px;background:linear-gradient(180deg,#7d8a6a,#3a88b8)}
.post-thumb.indoor{background:linear-gradient(180deg,#b79c7a,#7c8594)}
.post-title{left:520px;width:140px;font-size:7px;line-height:8.6px;font-weight:600;color:var(--green)}
.post-date{left:520px;font-size:7.2px;color:#ddd}
.f-sep{top:1035px;width:1px;height:72px;background:var(--footer-line)}
.c-title{font-size:8.8px;font-weight:600;letter-spacing:.7px;color:var(--green)}
.c-value{font-size:8.6px;letter-spacing:.8px;color:#eee;margin-top:1px}
.f-rule{left:57px;top:1107px;width:603px;height:1px;background:var(--footer-line)}
.f-legal{left:0;width:716px;text-align:center;font-size:7.2px;letter-spacing:.7px;font-weight:500;color:#eee}
.f-legal .green{color:var(--green)}
</style>
</head>
<body>

<!-- header -->
<div class="abs topbar"></div>
<div class="abs topbar-item" style="left:549px">
  <svg width="7" height="7" viewBox="0 0 10 10" fill="none" stroke="#fff" stroke-width="1"><circle cx="5" cy="3.2" r="2.2"/><path d="M1 9.5c0-2.2 1.8-3.6 4-3.6s4 1.4 4 3.6"/></svg>LOGIN</div>
<div class="abs topbar-item" style="left:590px">
  <svg width="7" height="7" viewBox="0 0 10 10" fill="none" stroke="#fff" stroke-width="1"><path d="M5 9 1.3 5.2A2.2 2.2 0 0 1 5 2.3a2.2 2.2 0 0 1 3.7 2.9Z"/></svg>WHISHLIST</div>
<div class="abs topbar-item" style="left:647px">EN <span style="font-size:4px">&#8964;</span></div>

<div class="abs brand"><span class="brand-mark"></span>StayHarbor</div>

<div class="abs nav-item active" style="left:396px">HOME</div>
<div class="abs nav-item" style="left:444px">SEARCH</div>
<div class="abs nav-item" style="left:499px">PROPERTY</div>
<div class="abs nav-item" style="left:561px">CUSTOM</div>
<div class="abs nav-item" style="left:618px">CONTACT US</div>

<!-- hero -->
<div class="abs hero" role="img" aria-label="Photo of a shopping street with a canal, a footbridge and hanging plants"></div>
<h2 class="abs hero-title">CONTACT US</h2>

<!-- main content -->
<div class="abs crumbs">Home Page &nbsp;/&nbsp; <b>Contact Us</b></div>
<h1 class="abs page-title">Contact Us</h1>
<p class="abs lead">Use this form to contact us regarding any topics other than specific property requests which should be done using the form on the property detail pages.</p>

<h3 class="abs office-name">Stayharbor</h3>
<div class="abs office-row" style="top:348px">
  <svg width="6" height="8" viewBox="0 0 6 8"><path d="M3 0a3 3 0 0 1 3 3c0 2-3 5-3 5S0 5 0 3a3 3 0 0 1 3-3Z" fill="#17b27c"/><circle cx="3" cy="3" r="1.1" fill="#fff"/></svg>
  <span>Via dei Tigli 24 50100 Valdorsa<br>Siena, Italy</span></div>
<div class="abs office-row" style="top:380px">
  <svg width="6" height="8" viewBox="0 0 6 8"><path d="M1 0h1.5l.6 2-1 .8c.4 1.3 1 2.2 2 2.9l.9-.7 1 1.7L4.8 8C2 7 .3 4 0 1Z" fill="#17b27c"/></svg>
  <span>Phone: +39 055 1184720</span></div>
<div class="abs office-row" style="top:402px">
  <svg width="8" height="8" viewBox="0 0 8 8"><rect x="0" y="2" width="8" height="6" fill="#17b27c"/><rect x="2" y="0" width="4" height="3" fill="#17b27c"/><rect x="3.5" y="3.5" width="3" height="3" fill="#fff"/></svg>
  <span>Fax: +39 055 1184721</span></div>
<div class="abs office-row" style="top:424px">
  <svg width="8" height="8" viewBox="0 0 8 8"><path d="M4 0 5 2.5 7.5 1.5 6 4l1.5 2.5L5 5.5 4 8 3 5.5.5 6.5 2 4 .5 1.5 3 2.5Z" fill="#17b27c"/></svg>
  <span>VAT Code: IT04471920336</span></div>

<!-- form -->
<div class="abs field" style="left:291px;top:321px;width:121px;height:21px">First Name:</div>
<div class="abs field" style="left:415px;top:321px;width:121px;height:21px">Last Name:</div>
<div class="abs field" style="left:539px;top:321px;width:121px;height:21px">Country:</div>
<div class="abs field" style="left:291px;top:346px;width:121px;height:21px">Email:</div>
<div class="abs field" style="left:415px;top:346px;width:121px;height:21px">Confirm Email:</div>
<div class="abs field" style="left:539px;top:346px;width:121px;height:21px">Phone:</div>
<div class="abs field tall" style="left:291px;top:372px;width:369px;height:66px">Message:</div>

<div class="abs subscribe"><span class="box"></span>I would like to subscribe to your newsletter.</div>

<div class="abs captcha">
  <span class="abs box" style="left:4px;top:7px;border-color:#888"></span>
  <span class="abs" style="left:16px;top:8.5px;font-size:3.8px;color:#333">I'm not a robot</span>
  <span class="abs" style="left:71px;top:3px;width:9px;height:9px;border-radius:50%;border:1.5px solid #4a7fd6"></span>
  <span class="abs" style="left:70px;top:14px;font-size:2.6px;color:#777">Verify now</span>
</div>

<div class="abs send">SEND</div>

<!-- map -->
<div class="abs map" role="img" aria-label="Street map showing the office location and nearby businesses"></div>

<!-- footer -->
<footer class="abs footer"></footer>
<div class="abs f-brand"><span class="dot"></span>StayHarbor</div>
<div class="abs f-sub">Subscribe to our Newsletter</div>
<div class="abs f-sub-line"></div>
<svg class="abs" style="left:194px;top:942px" width="24" height="8" viewBox="0 0 24 8" fill="none" stroke="#17b27c" stroke-width="0.8"><path d="M0 4h23M19 1l3.5 3L19 7"/></svg>
<p class="abs f-text">Our range of services is very large, and we are constantly expanding it.</p>

<div class="abs f-head" style="left:308px">Navigation</div>
<div class="abs f-link" style="top:902px">Last Minute</div>
<div class="abs f-link" style="top:923px">Special Offers</div>
<div class="abs f-link" style="top:944px">Experience</div>
<div class="abs f-link" style="top:964px">Contact Us</div>

<div class="abs f-head" style="left:472px">Recent posts</div>
<div class="abs post-thumb" style="top:903px" role="img" aria-label="Photo of a garden pool with sun loungers"></div>
<div class="abs post-title" style="top:903px">Which construction tool is better to choose?</div>
<div class="abs post-date" style="top:929px">2 November, 2020</div>
<div class="abs post-thumb indoor" style="top:954px" role="img" aria-label="Photo of a rustic room with a table tennis table"></div>
<div class="abs post-title" style="top:954px">Which construction tool is better to choose?</div>
<div class="abs post-date" style="top:980px">2 November, 2020</div>

<div class="abs f-sep" style="left:259px"></div>
<div class="abs f-sep" style="left:456px"></div>

<svg class="abs" style="left:72px;top:1050px" width="18" height="18" viewBox="0 0 18 18"><path d="M2 1h4l1.3 4-2.2 1.7c.9 2.6 2.5 4.4 5 5.6l1.8-2.1 4 1.6V16c-7.5-.5-13.4-6.5-14-14Z" fill="#17b27c"/></svg>
<div class="abs" style="left:98px;top:1051px"><div class="c-title">Call us</div><div class="c-value">+1 555 013 2290 (USA)</div></div>

<svg class="abs" style="left:289px;top:1052px" width="25" height="18" viewBox="0 0 25 18" fill="none" stroke="#17b27c" stroke-width="1.3"><rect x="1" y="1" width="23" height="16" rx="1.5"/><path d="m1.5 2 11 8 11-8"/></svg>
<div class="abs" style="left:320px;top:1051px"><div class="c-title">Write to us</div><div class="c-value">hello@stayharbor.test</div></div>

<svg class="abs" style="left:492px;top:1050px" width="18" height="25" viewBox="0 0 18 25" fill="none" stroke="#17b27c" stroke-width="1.3"><path d="M9 1a8 8 0 0 1 8 8c0 6-8 15-8 15S1 15 1 9a8 8 0 0 1 8-8Z"/><circle cx="9" cy="9" r="3.5"/></svg>
<div class="abs" style="left:513px;top:1051px"><div class="c-title">Office location</div><div class="c-value">18 Willow Lane, Harborview, NY 10990</div></div>

<div class="abs f-rule"></div>
<div class="abs f-legal" style="top:1122px">Privacy Policies &nbsp;&nbsp;/&nbsp;&nbsp; Reservation Policies &nbsp;&nbsp;/&nbsp;&nbsp; Cookie Policy</div>
<div class="abs f-legal" style="top:1133px">Copyright © 2021 StayHarbor. All Rights Reserved. <span class="green">Powered by StayHarbor</span></div>

<span class="abs" style="left:345px;top:1155px;width:10px;height:10px;border-radius:50%;background:#fff"></span>
<span class="abs" style="left:358px;top:1156px;width:32px;height:8px;background:#3b6fd8;border-radius:1px"></span>

</body>
</html>
```